Indonesian B2B Company (Bawo Ingredients) - Stationery Design

Bawo Ingredients needs a corporate, bold and professional-looking stationery design.

Bawo Ingredients is a new Indonesian company manufacturing, marketing and distributing various ingredients / raw materials such as flavours, fragrance, colours, sweeteners, preservatives for the food & beverage, pharmaceutical, personal care and other household goods industries.

It is a business to business (B2B) company as we supply various natural and synthetic raw materials to various consumer goods manufacturers. We therefore need a logo/identity with corporate and industrial style.

Bawo Ingredients is a startup company which belongs to a larger Tunas Mekar group of companies (http://tunasmekar.examplebiz.net/about) that focuses in the mining, petroleum and energy businesses. Bawo Ingredients would like to focus in providing good quality, safe, reliable and affordable ingredients for the industries. Our tagline is "Ingredients for Your Success"
Updates

We have updated some information including our requirements and contact details to be shown in the stationery. Please check the project brief.

Regards,

Bawo Ingredients

Target Market(s)

Manufacturers of food & beverages, personal care, pharmaceutical and other FMCG factories.

Industry/Entity Type

Business

Requirements
Must have
• Smart, professional and corporate touches in the stationery designs. We require designs for:
1. Letterhead
2. Envelope (with and without window)
3. Name card
4. Powerpoint presentation template
5. CD label
6. Small memo / with compliments card

Contact details:

Company name:
PT Bawo Ingredients

Address:
Ruko Puri Lestari Selatan, Blok F07 no: 11-12
Sunter Jaya Utara, 14350
Indonesia

Tel:+62 21 638 2097
Fax:+62 21 638 2096
Email: info@bawo-ingredients.co.id
Website: www.bawo-ingredients.co.id

```html
<!DOCTYPE html>
<html lang="en">
<head>
<meta charset="utf-8">
<title>Bawo Ingredients – Stationery</title>
<link href="https://fonts.googleapis.com/css2?family=PT+Sans:wght@400;700&display=swap" rel="stylesheet">
<style>
  :root {
    --stage: #1d1d1d;
    --brand-red: #d7262f;
    --brand-blue: #1b78c8;
    --brand-blue-light: #3592de;
    --brand-blue-dark: #1466b0;
    --brand-yellow: #f6b21b;
    --ink: #333333;
    --paper: #ffffff;
    --window: #6b6b6b;
    --label: #f2f2f2;
  }
  * { margin: 0; padding: 0; box-sizing: border-box; }
  html, body { width: 1200px; height: 749px; overflow: hidden; background: var(--stage); }
  body { position: relative; font-family: "PT Sans", Arial, sans-serif; }
  .abs { position: absolute; }

  .name-mark { display: flex; align-items: center; white-space: nowrap; font-weight: 400; }
  .name-mark .dot { display: inline-block; background: var(--brand-blue); flex: none; }
  .on-dark { color: var(--label); }
  .on-paper { color: var(--ink); }
  .on-blue { color: var(--paper); }
  .on-blue .dot { background: var(--paper); }

  /* Main name */
  .main-name { left: 78px; top: 192px; font-size: 30px; }
  .main-name .dot { width: 22px; height: 22px; margin-right: 12px; }

  .item-label { color: var(--label); font-size: 15px; white-space: nowrap; }

  /* Business card front */
  .card-front { left: 286px; top: 48px; width: 186px; height: 116px; background: var(--paper); }
  .card-front .person { position: absolute; left: 30px; top: 44px; text-align: center; }
  .card-front .person-name { color: var(--brand-blue); font-size: 8px; font-weight: 700; }
  .card-front .person-title { color: var(--ink); font-size: 5px; }
  .card-front .details { position: absolute; left: 98px; top: 10px; font-size: 4.4px; line-height: 5.4px; color: var(--ink); }
  .card-front .details .key { color: var(--brand-blue); }
  .card-front .details p { margin-bottom: 2px; }
  .card-front .name-mark { position: absolute; left: 10px; top: 83px; font-size: 7.5px; }
  .card-front .name-mark .dot { width: 6px; height: 6px; margin-right: 4px; }
  .card-front .band { position: absolute; left: 94px; top: 89px; width: 92px; height: 5px; background: var(--brand-blue); }

  /* Business card back */
  .card-back { left: 404px; top: 160px; width: 159px; height: 113px;
    background: linear-gradient(120deg, var(--brand-blue-light), var(--brand-blue-dark)); }
  .card-back .name-mark { position: absolute; left: 16px; top: 88px; font-size: 9px; }
  .card-back .name-mark .dot { width: 7px; height: 7px; margin-right: 4px; }

  /* Envelope */
  .envelope { left: 74px; top: 303px; width: 518px; height: 366px;
    background: linear-gradient(120deg, var(--brand-blue-light) 0%, var(--brand-blue) 55%, var(--brand-blue-dark) 100%); }
  .envelope .name-mark { position: absolute; left: 38px; top: 72px; font-size: 14px; }
  .envelope .name-mark .dot { width: 11px; height: 11px; margin-right: 6px; }
  .envelope .window { position: absolute; left: 36px; top: 108px; width: 263px; height: 99px;
    background: var(--window); border: 1px solid #2b2b2b; border-radius: 4px; }
  .envelope .env-contact { position: absolute; left: 37px; top: 224px; color: var(--paper);
    font-size: 10px; line-height: 11.5px; }
  .envelope .env-contact p { margin-bottom: 11px; }

  /* Letterhead */
  .letterhead { left: 646px; top: 9px; width: 474px; height: 680px; background: var(--paper); }
  .stripes { position: absolute; width: 17px; display: flex; }
  .stripes span { flex: 1; }
  .stripes .blue { background: var(--brand-blue); }
  .stripes .yellow { background: var(--brand-yellow); }
  .stripes .red { background: var(--brand-red); }
  .stripes-top { right: 0; top: 0; height: 302px; }
  .stripes-bottom { left: 0; top: 304px; height: 376px; }
  .letterhead .name-mark { position: absolute; left: 37px; top: 80px; font-size: 15px; }
  .letterhead .name-mark .dot { width: 11px; height: 11px; margin-right: 6px; }
  .letterhead .lh-footer { position: absolute; top: 628px; font-size: 8.5px; line-height: 10.5px; color: var(--ink); }
  .letterhead .lh-address { left: 37px; }
  .letterhead .lh-contact { left: 320px; }
</style>
</head>
<body>

  <div class="abs name-mark on-dark main-name"><span class="dot"></span>Bawo Ingredients</div>

  <section class="abs card-front" aria-label="Business card front">
    <div class="person">
      <div class="person-name">Adi Prasetyo</div>
      <div class="person-title">Post Title</div>
    </div>
    <div class="details">
      <p><span class="key">Address:</span><br>Ruko Puri Lestari Selatan,<br>Blok F07 no: 11-12 Sunter<br>Jaya Utara, 14350<br>Indonesia.</p>
      <p><span class="key">Web/Email:</span><br>info@bawo-ingredients.co.id<br>www.bawo-ingredients.co.id</p>
      <p><span class="key">Phone:</span><br>+62 21 638 2096 , +62 21 638 2097</p>
    </div>
    <div class="name-mark on-paper"><span class="dot"></span>Bawo Ingredients</div>
    <div class="band"></div>
  </section>
  <div class="abs item-label" style="left:488px; top:102px;">Business Card</div>

  <section class="abs card-back" aria-label="Business card back">
    <div class="name-mark on-blue"><span class="dot"></span>Bawo Ingredients</div>
  </section>

  <section class="abs envelope" aria-label="Envelope">
    <div class="name-mark on-blue"><span class="dot"></span>Bawo Ingredients</div>
    <div class="window"></div>
    <div class="env-contact">
      <p>Address:<br>Ruko Puri Lestari Selatan, Blok F07<br>no: 11-12 Sunter Jaya Utara,<br>14350 Indonesia.</p>
      <p>Web/Email:<br>info@bawo-ingredients.co.id<br>www.bawo-ingredients.co.id</p>
      <p>Phones:<br>+62 21 638 2096 , +62 21 638 2097</p>
    </div>
  </section>
  <div class="abs item-label" style="left:280px; top:690px;">Envelop</div>

  <section class="abs letterhead" aria-label="Letterhead">
    <div class="stripes stripes-top"><span class="blue"></span><span class="yellow"></span><span class="red"></span></div>
    <div class="stripes stripes-bottom"><span class="red"></span><span class="yellow"></span><span class="blue"></span></div>
    <div class="name-mark on-paper"><span class="dot"></span>Bawo Ingredients</div>
    <div class="lh-footer lh-address">Ruko Puri Lestari Selatan, Blok F07 no: 11-12<br>Sunter Jaya Utara, 14350<br>Indonesia.</div>
    <div class="lh-footer lh-contact">Tel:+62 21 638 2097<br>Fax:+62 21 638 2096<br>Website: www.bawo-ingredients.co.id<br>Email: info@bawo-ingredients.co.id</div>
  </section>
  <div class="abs item-label" style="left:833px; top:702px;">Letter Head</div>

</body>
</html>
```